I need a label with logo to go on jars of honey.
Label size 70mm x 70mm
The front label should say :
The Fenwick Honey Co. (logo)
Tarapeka Honey
400g
The back label:
Would have nutritional information
And our address
You can see from the uploaded files the styles I prefer, I have uploaded a photo of the honey product too. The background of the logo doesn't have to be white. I would like to develop a color scheme that would look nice against the color of the honey.
Logo Text
The Fenwick Honey Co. / The Fenwick Honey Company

```html
<!DOCTYPE html>
<html lang="en">
<head>
<meta charset="utf-8">
<title>Tarapeka Honey – Jar Label</title>
<link rel="stylesheet" href="https://fonts.googleapis.com/css2?family=Righteous&family=Barlow+Semi+Condensed:wght@600;700&display=swap">
<style>
  :root {
    --backdrop: #e9e9e9;
    --label-white: #f4f4f4;
    --band-gold: #f2b236;
    --band-stripe: #f6c25a;
    --comb-amber: #f0a93a;
    --comb-amber-deep: #e38f24;
    --comb-pale: #f3dfc4;
    --comb-pale-deep: #ecd2b0;
    --ink-dark: #2e2e2e;
    --ink-grey: #9a9a9a;
    --honey-yellow: #f2cf3c;
    --honey-orange: #ef9a35;
    --honey-red: #d2452a;
    --dipper-gold: #e9a449;
    --dipper-brown: #c9772a;
  }
  * { box-sizing: border-box; margin: 0; padding: 0; }
  html, body {
    width: 1200px;
    height: 960px;
    overflow: hidden;
    background: var(--backdrop);
  }
  .canvas {
    position: relative;
    width: 1200px;
    height: 960px;
  }
  .label {
    position: absolute;
    left: 280px;
    top: 85px;
    width: 640px;
    height: 790px;
    background: var(--label-white);
    overflow: hidden;
    box-shadow: 0 6px 24px rgba(0,0,0,0.08);
  }
  .brand-band {
    position: absolute;
    left: 0; top: 0;
    width: 100%;
    height: 118px;
    background:
      repeating-linear-gradient(115deg, var(--band-gold) 0 6px, var(--band-stripe) 6px 9px);
    display: flex;
    align-items: center;
    justify-content: center;
  }
  .brand-name {
    font-family: "Barlow Semi Condensed", sans-serif;
    font-weight: 600;
    font-size: 27px;
    line-height: 1.05;
    color: var(--ink-dark);
    text-align: center;
  }
  .comb-top {
    position: absolute;
    left: 0; top: 118px;
    width: 100%;
    height: 112px;
    background: linear-gradient(180deg, var(--comb-amber) 0%, var(--comb-amber-deep) 55%, rgba(240,169,58,0) 100%);
    opacity: 0.85;
  }
  .product-title {
    position: absolute;
    left: 46px;
    top: 240px;
    font-family: "Righteous", sans-serif;
    font-size: 104px;
    line-height: 1.55;
    text-transform: uppercase;
    letter-spacing: 1px;
  }
  .title-origin {
    display: block;
    background: linear-gradient(180deg, var(--ink-grey) 0%, var(--ink-dark) 70%);
    -webkit-background-clip: text;
    background-clip: text;
    color: transparent;
  }
  .title-product {
    display: block;
    background: linear-gradient(180deg, var(--honey-yellow) 0%, var(--honey-orange) 55%, var(--honey-red) 100%);
    -webkit-background-clip: text;
    background-clip: text;
    color: transparent;
  }
  .dipper-art {
    position: absolute;
    right: 0;
    top: 355px;
    width: 112px;
    height: 265px;
    border-radius: 112px 0 0 112px;
    background: radial-gradient(circle at 60% 55%, var(--dipper-gold) 0%, var(--dipper-brown) 80%);
  }
  .comb-bottom {
    position: absolute;
    left: 0; bottom: 0;
    width: 100%;
    height: 180px;
    background: linear-gradient(180deg, rgba(243,223,196,0) 0%, var(--comb-pale) 30%, var(--comb-pale-deep) 100%);
  }
  .net-weight {
    position: absolute;
    left: 0;
    bottom: 36px;
    width: 100%;
    text-align: center;
    font-family: "Barlow Semi Condensed", sans-serif;
    font-weight: 700;
    font-size: 46px;
    letter-spacing: 1px;
    color: var(--ink-dark);
  }
</style>
</head>
<body>
  <main class="canvas">
    <section class="label">
      <header class="brand-band">
        <p class="brand-name">The Fenwick<br>Honey Co.</p>
      </header>
      <div class="comb-top" role="img" aria-label="Amber honeycomb pattern along the top of the label"></div>
      <h1 class="product-title">
        <span class="title-origin">Tarapeka</span>
        <span class="title-product">Honey</span>
      </h1>
      <div class="dipper-art" role="img" aria-label="Illustration of a honey dipper dripping honey with a bee"></div>
      <div class="comb-bottom" role="img" aria-label="Pale honeycomb pattern along the bottom of the label"></div>
      <p class="net-weight">400G</p>
    </section>
  </main>
</body>
</html>
```